business card deign

Logo needs the following on it.
1. attached logo
2. Tagline - "If it keeps a drink cold or the party going...we do it!"
3. Name- Dalton Pikes, Founder and CPO
4. Address - 412 E. Carver Avenue, Ste 2207, Tampa, FL. 33917
5. Phone - 555.318.4726

```html
<!DOCTYPE html>
<html lang="en">
<head>
<meta charset="utf-8">
<title>Coolvale Business Card</title>
<link rel="stylesheet" href="https://fonts.googleapis.com/css2?family=Montserrat:wght@400;500;700&display=swap">
<style>
  :root {
    --stage: #9a9a9a;
    --card-light: #ffffff;
    --card-dark: #2a2a2a;
    --ink: #2b2b2b;
    --ink-soft: #3a3a3a;
    --paper-text: #ffffff;
    --faint: #ececec;
  }
  * { margin: 0; padding: 0; box-sizing: border-box; }
  html, body {
    width: 1200px; height: 1059px; overflow: hidden;
    background: var(--stage);
    font-family: "Montserrat", Arial, sans-serif;
  }
  .canvas { position: relative; width: 1200px; height: 1059px; }
  .card {
    position: absolute;
    border-radius: 18px;
    overflow: hidden;
  }
  .card--front {
    left: 256px; top: 89px; width: 688px; height: 390px;
    background: var(--card-light);
    color: var(--ink);
  }
  .card--back {
    left: 253px; top: 569px; width: 694px; height: 394px;
    background: var(--card-dark);
    color: var(--paper-text);
  }
  .brand-dot {
    position: absolute;
    border-radius: 50%;
  }
  .card--front .brand-dot {
    left: 62px; top: 36px; width: 92px; height: 92px;
    background: var(--ink);
  }
  .card--back .brand-dot {
    left: 277px; top: 86px; width: 140px; height: 140px;
    background: var(--paper-text);
  }
  .backdrop-dot {
    position: absolute; left: 390px; top: 70px;
    width: 270px; height: 270px; border-radius: 50%;
    background: var(--faint);
  }
  .wordmark {
    font-weight: 700;
    text-transform: uppercase;
    white-space: nowrap;
    line-height: 1;
  }
  .card--front .wordmark {
    position: absolute; left: 38px; top: 142px;
    font-size: 19px; letter-spacing: 0.3em; color: var(--ink);
  }
  .card--back .wordmark {
    position: absolute; left: 0; right: 0; top: 254px;
    text-align: center; font-size: 31px;
    letter-spacing: 0.32em; padding-left: 0.32em;
  }
  .holder { position: absolute; left: 39px; top: 195px; }
  .holder__name {
    font-size: 23px; font-weight: 700; letter-spacing: 0.02em;
    text-transform: uppercase; line-height: 1;
  }
  .holder__title {
    margin-top: 5px; font-size: 15.5px; font-weight: 400; color: var(--ink-soft);
  }
  .holder__address {
    margin-top: 16px; font-size: 16px; line-height: 22px; color: var(--ink-soft);
    font-style: normal;
  }
  .contact { margin-top: 10px; list-style: none; }
  .contact li {
    display: flex; align-items: center; gap: 8px;
    font-size: 16px; color: var(--ink-soft); height: 26px;
  }
  .contact svg { width: 12px; height: 12px; fill: var(--ink); flex: none; }
  .tagline {
    position: absolute; left: 0; right: 0; top: 343px;
    text-align: center; font-size: 15.5px; font-weight: 400; letter-spacing: 0.01em;
  }
</style>
</head>
<body>
<main class="canvas">
  <section class="card card--front" aria-label="Card front">
    <div class="backdrop-dot" aria-hidden="true"></div>
    <div class="brand-dot" aria-hidden="true"></div>
    <div class="wordmark">Coolvale</div>
    <div class="holder">
      <h1 class="holder__name">Dalton Pikes</h1>
      <p class="holder__title">Founder and CPO</p>
      <address class="holder__address">412 E. Carver Avenue<br>Ste 2207, Tampa, FL. 33917</address>
      <ul class="contact">
        <li>
          <svg viewBox="0 0 24 24" aria-hidden="true"><path d="M3 9c0-3 4-5 9-5s9 2 9 5v2h-5V9c-1-1-3-1-4-1s-3 0-4 1v2H3zM6 12h12l2 8H4z"/></svg>
          <span>555.318.4726</span>
        </li>
        <li>
          <svg viewBox="0 0 24 24" aria-hidden="true"><path d="M2 10l10-7 10 7v11H2zM4 11l8 6 8-6-8-5z"/></svg>
          <span>dpikes@coolvale.com</span>
        </li>
      </ul>
    </div>
  </section>

  <section class="card card--back" aria-label="Card back">
    <div class="brand-dot" aria-hidden="true"></div>
    <div class="wordmark">Coolvale</div>
    <p class="tagline">If it keeps a drink cold or the party going...we do it!</p>
  </section>
</main>
</body>
</html>
```